Business card for medical clinic

I need an upmarket, modern medical/health business card for my clinic

Contact Information for Business Card

name, address, email, qr code

```html
<!DOCTYPE html>
<html lang="en">
<head>
<meta charset="utf-8">
<title>Veridan Health Partners – Business Card</title>
<link href="https://fonts.googleapis.com/css2?family=Poppins:wght@300;400;500;600;700&display=swap" rel="stylesheet">
<style>
  :root {
    --backdrop: #222224;
    --card: #1f2024;
    --accent: #1e9ad6;
    --ink: #f2f3f5;
    --ink-soft: #d9dbe0;
  }
  * { margin: 0; padding: 0; box-sizing: border-box; }
  html, body {
    width: 1200px; height: 711px; overflow: hidden;
    background: var(--backdrop);
    font-family: "Poppins", sans-serif;
  }
  .stage {
    position: relative; width: 1200px; height: 711px;
    display: flex; align-items: center; justify-content: center; gap: 40px;
  }
  .card {
    position: relative; width: 540px; height: 309px;
    background: var(--card);
    border-left: 4px solid var(--accent);
    border-bottom: 4px solid var(--accent);
    box-shadow: 0 14px 30px rgba(0,0,0,.55);
    overflow: hidden;
  }
  .brand { display: flex; align-items: center; gap: 10px; }
  .brand-name {
    display: flex; flex-direction: column;
    font-weight: 500; font-size: 16px; line-height: 1.25; letter-spacing: 1.5px;
    text-transform: uppercase; color: var(--ink); white-space: nowrap;
  }
  .brand-dot {
    width: 28px; height: 28px; border-radius: 50%;
    border: 2px solid var(--ink); flex: none;
  }
  /* back side */
  .card-back .brand { position: absolute; right: 40px; bottom: 50px; }
  /* front side */
  .card-front .brand { position: absolute; left: 34px; top: 128px; }
  .card-front .brand-name { color: var(--accent); font-size: 15px; }
  .card-front .brand-dot { border-color: var(--accent); }
  .divider {
    position: absolute; left: 284px; top: 50px; width: 1px; height: 210px;
    background: var(--accent);
  }
  .details { position: absolute; left: 306px; top: 50px; width: 210px; color: var(--ink); }
  .person-name { font-size: 27px; line-height: 1.05; color: var(--accent); white-space: nowrap; }
  .person-name .first { font-weight: 700; }
  .person-name .last { font-weight: 300; }
  .person-role { font-size: 12.5px; font-weight: 600; margin-top: 4px; }
  .address { font-size: 11.5px; font-weight: 400; line-height: 1.5; margin-top: 16px; color: var(--ink-soft); }
  .contact-list { list-style: none; margin-top: 16px; }
  .contact-list li {
    display: flex; align-items: center; gap: 8px;
    font-size: 11.5px; line-height: 1.9; color: var(--ink-soft); white-space: nowrap;
  }
  .contact-icon { width: 13px; height: 13px; flex: none; }
</style>
</head>
<body>
<main class="stage">
  <section class="card card-back" aria-label="Card back">
    <div class="brand">
      <span class="brand-dot"></span>
      <span class="brand-name"><span>Veridan Health</span><span>Partners</span></span>
    </div>
  </section>

  <section class="card card-front" aria-label="Card front">
    <div class="brand">
      <span class="brand-dot"></span>
      <span class="brand-name"><span>Veridan Health</span><span>Partners</span></span>
    </div>
    <div class="divider"></div>
    <div class="details">
      <h1 class="person-name"><span class="first">Marta</span> <span class="last">Kovel</span></h1>
      <p class="person-role">Founder &amp; CEO</p>
      <p class="address">1840 Linden Ave. Suite 300<br>Oakridge, TX 75230</p>
      <ul class="contact-list">
        <li>
          <svg class="contact-icon" viewBox="0 0 24 24" aria-hidden="true"><path fill="var(--accent)" d="M6.6 10.8a15.1 15.1 0 0 0 6.6 6.6l2.2-2.2c.3-.3.7-.4 1-.2 1.1.4 2.3.6 3.6.6.6 0 1 .4 1 1V20c0 .6-.4 1-1 1A17 17 0 0 1 3 4c0-.6.4-1 1-1h3.5c.6 0 1 .4 1 1 0 1.3.2 2.5.6 3.6.1.3 0 .7-.2 1z"/></svg>
          (555) 214-0387
        </li>
        <li>
          <svg class="contact-icon" viewBox="0 0 24 24" aria-hidden="true"><rect x="2" y="5" width="20" height="14" rx="2" fill="var(--accent)"/><path d="M3 6l9 7 9-7" stroke="var(--card)" stroke-width="1.8" fill="none"/></svg>
          info@veridanclinic.com
        </li>
        <li>
          <svg class="contact-icon" viewBox="0 0 24 24" aria-hidden="true"><circle cx="12" cy="12" r="9.5" fill="none" stroke="var(--accent)" stroke-width="2"/><ellipse cx="12" cy="12" rx="4" ry="9.5" fill="none" stroke="var(--accent)" stroke-width="1.6"/><path d="M2.5 12h19" stroke="var(--accent)" stroke-width="1.6"/></svg>
          www.veridanclinic.com
        </li>
      </ul>
    </div>
  </section>
</main>
</body>
</html>
```